Church Website with Home Page and Member Sermon Library

I am in need of an updated design for our church website. This will include 4 pages (outlined below). We are a conservative, evangelical, Christian church. The site should be modern and clean, while still reflecting our conservative values. I already have a logo for our church, and I want the site to incorporate the logo, and match the logo/branding. Stock photos are allowed if needed, but I have uploaded some images of our church and would prefer those images to be used if possible. Any stock photos used should not include any people in the photos (scenery, nature, buildings, animals, etc. are fine).

The site will need 4 pages: Home, Support Us (Donate), Login, and Recording Library.

Page 1: Home
The home page should include the following sections:

- Navigation: Should include links to each section of the home page plus a "listen live" link which will take the user to a live-streaming site and a "support us" link which will take the user to a support/donate page.

- Announcements: Can be either a banner or some other design, but there needs to be some way for us to post announcements for visitors to see. I'm open for creative ideas in this section, but would like it not to take up a lot of room on the page.

- About Us: Should include address, service times (see attached document), and information about the church.

- Pastor Bio: A section that introduces our pastor and gives a short bio about our pastor. Would like this section to include a picture of our pastor. Somewhere in this section I would like to include this Bible reference: "And I will give you pastors according to mine heart, which shall feed you with knowledge and understanding. Jer 3:15 LPW"

- Articles of Faith (What We Believe): This should include several sub-sections each with a heading, body, and possibly 1 or more scripture references. I have attached a document to the brief that includes our articles of faith. Feel free to be creative with this section in how you lay these out and format them.

- Support Us: A small section that explains what kind of support someone can give and a link to a donation page. The link can say something like "Support Us" or "Donate Now".

- Contact form: A contact form that allows the visitor to send us a message. The contact form should ask for name, email, phone, and message.

- Footer: A footer that will be displayed on all pages of the site. This should include at a minimum a link to the home page (or a link to each individual section in the home page if you prefer), a link to "listen live", a link to "support us", a link to "contact us" (or you can put the contact form directly in the footer if you prefer), the address, and a "member login" link.

Page 2: Support Us
The donation page should include a form the visitor can fill out to make a donation. We will embed a third party form later. For this design, please just mock out the design with a basic form asking for name, phone, and email.

Page 3: Login
The recording library (detailed below) will require members to login with a shared numeric code before accessing the page. We need a design for a login screen. The screen should include navigation/footer just like all other pages, but the body of the login page will consist only of a form that asks the user to enter the access code and then a "login" button.

Page 4: Recording Library

The library page is a member-only page that will require a shared, numeric pass code to access. On this page, members will be able to access a filterable list of past sermons. The page by default should display most recent sermons, but should also include a search form that allows the member to filter the sermon list to find a particular sermon. The search form should allow the user to select a filter type (e.g. Speaker name, date, event, etc.) and type in a value to search. They should be able to add multiple filters and remove filters that have been added. Each sermon that is displayed in the result list should include basic information such as title, date, speaker, tags, etc. along with a download icon, and an embedded audio player where they can click a play button to stream it on-demand. Each sermon should also have clickable tags associated with it that can be used to find related sermons.
Updates

I have uploaded several images of our church. Feel free to incorporate these into your design if possible.

Target Market(s)

Church Members

Industry/Entity Type

Religion

Number of Pages Required

4 page

Font styles to use
Sans Serif

Colors

Designer to choose colors to be used in the design.

Requirements
Must have
• Must incorporate the logo (attached)
Nice to have
• Would like the design to incorporate pictures of our church (attached) instead of stock photos if possible.
Should not have
• Please avoid an overly cluttered design. Stock photos used should not include any people in the photos.

```html
<!DOCTYPE html>
<html lang="en">
<head>
<meta charset="utf-8">
<title>Cedar Hill Church – Donation</title>
<link href="https://fonts.googleapis.com/css2?family=Cinzel:wght@400;600&family=Montserrat:wght@400;500;600&display=swap" rel="stylesheet">
<style>
:root{
  --green:#7a9a66;
  --ink:#2b2b2b;
  --muted:#8a8a8a;
  --line:#e3e3e3;
  --field:#dcdcdc;
  --footer:#1f2226;
  --footer-text:#b9bcc0;
  --white:#ffffff;
}
*{box-sizing:border-box;margin:0;padding:0}
html,body{width:723px;height:1200px;overflow:hidden}
body{position:relative;background:var(--white);font-family:"Montserrat",Arial,sans-serif;color:var(--ink)}

.hero{position:absolute;left:0;top:0;width:723px;height:272px;
  background:linear-gradient(90deg,#1e3442 0%,#3a3226 30%,#22342c 60%,#3a2424 100%);}
.hero-shade{position:absolute;inset:0;background:linear-gradient(rgba(8,10,14,.35),rgba(8,10,14,.55))}
.brand{position:absolute;left:44px;top:34px;display:flex;align-items:center;gap:8px;
  font-family:"Montserrat",Arial,sans-serif;font-weight:600;font-size:12px;letter-spacing:1px;color:var(--white)}
.brand .mark{width:12px;height:12px;border:2px solid var(--white)}
.nav{position:absolute;right:44px;top:34px;display:flex;align-items:center;gap:22px;font-size:10px;font-weight:500;color:var(--white);letter-spacing:.5px}
.btn{display:inline-block;background:var(--green);color:var(--white);font-size:10px;font-weight:500;padding:6px 12px;letter-spacing:.5px}
.page-title{position:absolute;top:145px;width:100%;text-align:center;font-family:"Cinzel",serif;font-weight:400;font-size:42px;letter-spacing:3px;color:var(--white)}

.login-hint{position:absolute;left:160px;top:318px;font-size:10.5px;color:var(--ink)}
.card{position:absolute;left:168px;width:392px;border:1px solid var(--line);padding:14px 14px}
.card h2{font-size:8.5px;font-weight:600;letter-spacing:.8px;text-transform:uppercase;margin-bottom:10px}
.donation{top:350px;height:120px}
.amounts{display:flex;border:1px solid var(--line)}
.amounts span{flex:1;text-align:center;font-size:8.5px;color:var(--muted);padding:7px 0}
.amounts .is-selected{background:var(--green);color:var(--white)}
.label{font-size:8px;color:var(--muted);text-transform:uppercase;letter-spacing:.5px;display:block;margin:12px 0 5px}
.field{height:22px;border-bottom:1px solid var(--field);font-size:8px;color:#c4c4c4;padding:6px 2px}
.details{top:488px;height:234px}
.row{display:flex;gap:18px;margin-bottom:12px}
.row > div{flex:1}
.row .label{margin:0 0 4px;text-transform:none;font-size:8.5px}
.payment{top:742px;height:170px}
.option{display:flex;gap:10px;margin:18px 0 0 6px}
.radio{width:11px;height:11px;border:1px solid #999;border-radius:50%;flex:none;margin-top:1px}
.radio.on{border:3px solid var(--ink)}
.option strong{font-size:8.5px;font-weight:600;display:block;margin-bottom:4px}
.option p{font-size:7.5px;color:var(--muted);line-height:1.4}
.cards{display:flex;gap:10px;margin-top:4px}
.cards span{font-size:7.5px;font-weight:500;color:var(--ink)}
.submit{position:absolute;left:160px;top:925px}

.footer{position:absolute;left:0;top:1007px;width:723px;height:193px;background:var(--footer);color:var(--footer-text)}
.footer-brand{position:absolute;left:70px;top:58px;display:flex;align-items:center;gap:8px;font-size:12px;font-weight:600;letter-spacing:1px;color:var(--white)}
.footer-brand .mark{width:12px;height:12px;border:2px solid var(--white)}
.col{position:absolute;top:50px}
.col h3{font-family:"Cinzel",serif;font-weight:400;font-size:14px;color:var(--white);letter-spacing:1px;margin-bottom:14px}
.col p,.col li{font-size:8px;line-height:1.6}
.contact{left:299px;width:160px}
.contact ul{list-style:none}
.contact li{display:flex;gap:6px;align-items:flex-start;margin-bottom:5px}
.contact svg{flex:none;margin-top:2px}
.give{left:477px;width:160px}
.give .btn{margin-top:10px}
.bottom{position:absolute;left:44px;right:44px;bottom:12px;display:flex;justify-content:space-between;align-items:center;font-size:7.5px}
.social{display:flex;gap:8px}
.social span{width:8px;height:8px;border-radius:50%;background:var(--footer-text)}
</style>
</head>
<body>

<header class="hero">
  <div class="hero-shade" role="img" aria-label="Photo of stained glass windows inside the church"></div>
  <div class="brand"><span class="mark"></span>CEDAR HILL CHURCH</div>
  <nav class="nav"><span>HOME</span><span>LIBRARY</span><span class="btn">DONATE</span></nav>
  <h1 class="page-title">DONATION</h1>
</header>

<p class="login-hint">Registered before? Log in to use your saved details.</p>

<section class="card donation">
  <h2>Your donation</h2>
  <div class="amounts"><span>$50.00</span><span class="is-selected">$55.00</span><span>$100.00</span></div>
  <span class="label">Custom amount</span>
  <div class="field">$0.00</div>
</section>

<section class="card details">
  <h2>Details</h2>
  <div class="row"><div><span class="label">First name *</span><div class="field"></div></div><div><span class="label">Last name *</span><div class="field"></div></div></div>
  <div class="row"><div><span class="label">Email *</span><div class="field"></div></div><div><span class="label">Phone</span><div class="field"></div></div></div>
  <div class="row"><div><span class="label">Address</span><div class="field"></div></div></div>
  <div class="row"><div><span class="label">City</span><div class="field"></div></div><div><span class="label">Postcode</span><div class="field"></div></div></div>
</section>

<section class="card payment">
  <h2>Choose your payment method</h2>
  <div class="option"><span class="radio"></span><div><strong>QuickPay</strong><p>You'll be redirected to QuickPay to complete<br>your payment.</p></div></div>
  <div class="option"><span class="radio on"></span><div><strong>Credit / Debit Card</strong><div class="cards"><span>NovaCard</span><span>OrbitPay</span></div></div></div>
</section>

<span class="btn submit">DONATE</span>

<footer class="footer">
  <div class="footer-brand"><span class="mark"></span>CEDAR HILL CHURCH</div>
  <div class="col contact">
    <h3>CONTACT</h3>
    <ul>
      <li><svg width="7" height="9" viewBox="0 0 7 9"><path d="M3.5 0a3.5 3.5 0 0 0-3.5 3.5C0 6 3.5 9 3.5 9S7 6 7 3.5A3.5 3.5 0 0 0 3.5 0z" fill="currentColor"/></svg>2410 Meadow Lane, Cedar Hill,<br>Ontario 48210</li>
      <li><svg width="7" height="7" viewBox="0 0 7 7"><path d="M1 0l1.5 1.8-1 1c.5 1 1.2 1.7 2.2 2.2l1-1L7 5.5 6 7C3 7 0 4 0 1z" fill="currentColor"/></svg>+1 555 204 8812</li>
      <li><svg width="8" height="6" viewBox="0 0 8 6"><rect x=".5" y=".5" width="7" height="5" fill="none" stroke="currentColor"/><path d="M.5.5L4 3.5 7.5.5" fill="none" stroke="currentColor"/></svg>hello@cedarhillchurch.org</li>
    </ul>
  </div>
  <div class="col give">
    <h3>DONATION</h3>
    <p>Your gift supports our ministry, outreach and weekly services in our community.</p>
    <span class="btn">DONATE</span>
  </div>
  <div class="bottom">
    <span>Copyright 2022 Cedar Hill Church | All rights reserved</span>
    <div class="social"><span></span><span></span><span></span><span></span></div>
  </div>
</footer>

</body>
</html>
```